Business Card Design Project

I need a business card designed from scratch. I have an existing logo that I can upload in Illustrator for modification or redesign.

The Company is called Query Lanterns http://querylanterns.com.au and we provide Search Engine Optimization services to Australian businesses. The current logo signifies an increase in visitors, profits etc...

There are no restrictions as to the redesign - colours, style etc are all open to change.

Cards will be full colour and one sided printed at http://www.cardmoxel.com.au so check their requirements for file format and sizes etc.

I will expect all original files upon completion of project.

Target Market(s)

Any business with a web site looking to improve their search engine rankings

Industry/Entity Type

Business

Requirements
Must have
• I like modern, sleek designs. Clean, not fussy, uncluttered.

```html
<!DOCTYPE html>
<html lang="en">
<head>
<meta charset="utf-8">
<title>Query Lanterns – Business Card</title>
<link rel="stylesheet" href="https://fonts.googleapis.com/css2?family=Open+Sans:wght@400;600;700;800&display=swap">
<style>
  :root {
    --brand-blue: #1b6fb5;
    --brand-yellow: #f5c400;
    --ink-grey: #4a4a4a;
    --muted-grey: #6b6b6b;
    --card-white: #ffffff;
    --backdrop: #e9e6e2;
  }
  * { margin: 0; padding: 0; box-sizing: border-box; }
  html, body { width: 1200px; height: 460px; overflow: hidden; }
  body {
    background: var(--backdrop);
    font-family: "Open Sans", Arial, sans-serif;
    position: relative;
  }
  .card {
    position: absolute;
    width: 543px;
    height: 307px;
    background: var(--card-white);
    box-shadow: 0 2px 6px rgba(0,0,0,0.18);
  }
  .card--front { left: 42px; top: 78px; }
  .card--back { left: 634px; top: 76px; }

  .wordmark {
    position: absolute;
    display: flex;
    align-items: center;
    gap: 10px;
  }
  .wordmark__dot {
    width: 18px; height: 18px;
    border-radius: 50%;
    background: var(--brand-yellow);
    flex: none;
  }
  .wordmark__name {
    color: var(--brand-blue);
    font-weight: 800;
    white-space: nowrap;
    letter-spacing: -0.5px;
  }
  .card--front .wordmark { left: 40px; top: 52px; }
  .card--front .wordmark__name { font-size: 32px; }

  .accent-bar {
    position: absolute;
    width: 6px;
    background: var(--brand-blue);
  }
  .accent-bar--name { left: 0; top: 179px; height: 35px; }
  .accent-bar--contact { right: 19px; top: 184px; height: 89px; }

  .person { position: absolute; left: 24px; top: 181px; }
  .person__name { color: var(--brand-blue); font-weight: 700; font-size: 15.5px; line-height: 20px; }
  .person__title { color: var(--muted-grey); font-size: 12.5px; line-height: 17px; }

  .contact {
    position: absolute;
    right: 35px;
    top: 180px;
    list-style: none;
    text-align: right;
    color: var(--ink-grey);
    font-size: 12.5px;
  }
  .contact__item {
    display: flex;
    justify-content: flex-end;
    align-items: center;
    gap: 6px;
    height: 17.5px;
  }
  .contact__icon { width: 10px; height: 10px; flex: none; fill: var(--brand-blue); }
  .contact__address { margin-top: 5px; font-size: 13px; padding-right: 8px; }

  .card--back .wordmark {
    left: 50%; top: 96px;
    transform: translateX(-50%);
  }
  .card--back .wordmark__name { font-size: 34px; }
  .web-address {
    position: absolute;
    left: 0; right: 0; top: 228px;
    text-align: center;
    font-size: 13px;
    letter-spacing: 3px;
    color: var(--ink-grey);
  }
  .web-address__domain { color: var(--brand-blue); }
</style>
</head>
<body>
  <section class="card card--front" aria-label="Card front">
    <div class="wordmark">
      <span class="wordmark__dot"></span>
      <span class="wordmark__name">Query Lanterns</span>
    </div>

    <div class="accent-bar accent-bar--name"></div>
    <div class="person">
      <p class="person__name">Your Name</p>
      <p class="person__title">Title</p>
    </div>

    <ul class="contact">
      <li class="contact__item">098 765 4321
        <svg class="contact__icon" viewBox="0 0 10 10"><circle cx="5" cy="5" r="5"/><path d="M3 2.5c0 2.6 1.8 4.8 4.4 5l.4-1.2-1.3-.6-.5.6C5 5.9 4.2 5 4 4l.6-.5-.5-1.3z" fill="#fff"/></svg>
      </li>
      <li class="contact__item">098 765 4321
        <svg class="contact__icon" viewBox="0 0 10 10"><rect x="2.5" y="0.5" width="5" height="9" rx="1"/><rect x="3.4" y="1.6" width="3.2" height="5.4" fill="#fff"/></svg>
      </li>
      <li class="contact__item">enquiry@querylanterns.com.au
        <svg class="contact__icon" viewBox="0 0 10 10"><rect x="0.5" y="2" width="9" height="6.5"/><path d="M0.8 2.3L5 5.6l4.2-3.3" stroke="#fff" stroke-width="0.8" fill="none"/></svg>
      </li>
      <li class="contact__item">www.querylanterns.com.au
        <svg class="contact__icon" viewBox="0 0 10 10"><circle cx="5" cy="5" r="4.6"/><path d="M0.6 5h8.8M5 0.5c-2.4 2.6-2.4 6.4 0 9M5 0.5c2.4 2.6 2.4 6.4 0 9" stroke="#fff" stroke-width="0.6" fill="none"/></svg>
      </li>
      <li class="contact__item contact__address">00Floor Street, City Name State Name, Contry Name</li>
    </ul>
    <div class="accent-bar accent-bar--contact"></div>
  </section>

  <section class="card card--back" aria-label="Card back">
    <div class="wordmark">
      <span class="wordmark__dot"></span>
      <span class="wordmark__name">Query Lanterns</span>
    </div>
    <p class="web-address">www.<span class="web-address__domain">querylanterns</span>.com.au</p>
  </section>
</body>
</html>
```